Business Card for Professional Photographer

I'm looking for an eye catching modern clean design that compliments my logo/ website fonts & colours.
I specialise in architecture, corporate & commercial photography so I'm marketing to professional clients rather than portrait / wedding clients.

I would prefer to not have a solid black design.

My logo brand guide is as follows :

Main front font. : Reislust
Main font colour : #fff
Slogan front font : Ubuntu Bold
Monogram front font : Venti Medium
Container colour : #fff

I need print ready files in pdf .png & .eps formats.

Included in the files below are some screen grabs as reference to font & colours etc.

```html
<!DOCTYPE html>
<html lang="en">
<head>
<meta charset="utf-8">
<title>Lens and Line – Business Card</title>
<link rel="stylesheet" href="https://fonts.googleapis.com/css2?family=Ubuntu:wght@400;500&family=Saira+Semi+Condensed:wght@600&family=Roboto:wght@400&display=swap">
<style>
  :root {
    --backdrop: #b9b9b9;
    --gold-deep: #b8914a;
    --gold-mid: #d2b36c;
    --gold-light: #ece39c;
    --gold-text: #c49a52;
    --ink: #1b1b1b;
    --ink-soft: #2a2a2a;
    --card-white: #f7f7f5;
  }
  * { margin: 0; padding: 0; box-sizing: border-box; }
  html, body { width: 1200px; height: 576px; overflow: hidden; }
  body { background: var(--backdrop); position: relative; font-family: "Roboto", sans-serif; }

  .card {
    position: absolute;
    top: 138px;
    width: 484px;
    height: 294px;
    border-radius: 10px;
    overflow: hidden;
    box-shadow: 0 4px 8px rgba(0,0,0,0.25);
  }

  /* Front */
  .card-front {
    left: 82px;
    background: linear-gradient(200deg, var(--gold-light) 0%, var(--gold-mid) 55%, var(--gold-deep) 100%);
  }
  .brand-lockup {
    position: absolute;
    left: 0; right: 0;
    top: 112px;
    display: flex;
    justify-content: center;
    align-items: center;
    gap: 16px;
  }
  .brand-square {
    width: 34px; height: 34px;
    background: var(--ink);
  }
  .brand-name {
    font-family: "Ubuntu", sans-serif;
    font-weight: 500;
    font-size: 28px;
    letter-spacing: 0;
    color: var(--ink);
    line-height: 1;
  }
  .brand-tagline {
    font-family: "Ubuntu", sans-serif;
    font-weight: 400;
    font-size: 10px;
    letter-spacing: 0.4px;
    color: var(--ink);
    margin-top: 6px;
  }
  .front-web {
    position: absolute;
    left: 0; right: 0;
    top: 258px;
    text-align: center;
    font-family: "Ubuntu", sans-serif;
    font-size: 12.5px;
    letter-spacing: 2.2px;
    color: var(--ink-soft);
  }

  /* Back */
  .card-back {
    left: 602px;
    height: 292px;
    background: var(--card-white);
  }
  .back-title {
    position: absolute;
    left: 26px;
    top: 30px;
    font-family: "Ubuntu", sans-serif;
    font-weight: 500;
    font-size: 28px;
    color: var(--gold-text);
    line-height: 1;
  }
  .back-tagline {
    position: absolute;
    left: 27px;
    top: 64px;
    font-family: "Ubuntu", sans-serif;
    font-weight: 400;
    font-size: 10px;
    letter-spacing: 0.4px;
    color: var(--gold-text);
  }
  .info-band {
    position: absolute;
    left: 0; right: 0;
    top: 108px;
    height: 130px;
    background: linear-gradient(90deg, var(--gold-deep) 0%, var(--gold-mid) 60%, var(--gold-light) 100%);
  }
  .person-name {
    position: absolute;
    left: 26px;
    top: 16px;
    font-family: "Saira Semi Condensed", sans-serif;
    font-weight: 600;
    font-size: 20px;
    color: var(--ink);
    line-height: 1;
  }
  .person-role {
    position: absolute;
    left: 26px;
    top: 41px;
    font-size: 13.5px;
    color: var(--ink);
  }
  .contact-list {
    position: absolute;
    left: 26px;
    top: 68px;
    list-style: none;
  }
  .contact-list li {
    display: flex;
    align-items: center;
    height: 18.5px;
    font-size: 13.5px;
    color: var(--ink);
  }
  .contact-icon { width: 11px; height: 11px; margin-right: 13px; fill: var(--ink); }
  .back-address {
    position: absolute;
    left: 26px;
    top: 258px;
    font-size: 13.5px;
    color: var(--ink-soft);
  }
</style>
</head>
<body>

<section class="card card-front">
  <div class="brand-lockup">
    <div class="brand-square"></div>
    <div>
      <div class="brand-name">Lens and Line</div>
      <div class="brand-tagline">Spaces, People and Products</div>
    </div>
  </div>
  <div class="front-web">www.lensandline.com.au</div>
</section>

<section class="card card-back">
  <div class="back-title">Lens and Line</div>
  <div class="back-tagline">Spaces, People and Products</div>
  <div class="info-band">
    <div class="person-name">Reid Callan</div>
    <div class="person-role">Photographer</div>
    <ul class="contact-list">
      <li>
        <svg class="contact-icon" viewBox="0 0 12 12"><path d="M1 4c0-2 2-3 5-3s5 1 5 3v1H8.5V4h-5v1H1zM3 6h6l1.5 5h-9z"/></svg>
        0412558019
      </li>
      <li>
        <svg class="contact-icon" viewBox="0 0 12 12"><path d="M0 2h12v8H0z M1 3l5 3.5L11 3z" fill-rule="evenodd"/></svg>
        info@lensandline.com.au
      </li>
      <li>
        <svg class="contact-icon" viewBox="0 0 12 12"><circle cx="6" cy="6" r="5.5"/><path d="M0.5 6h11M6 0.5v11M2 3h8M2 9h8" stroke="#d2b36c" stroke-width="0.8" fill="none"/></svg>
        www.lensandline.com.au
      </li>
    </ul>
  </div>
  <div class="back-address">48 Harbour Rd Ashwood Vic 3147</div>
</section>

</body>
</html>
```